Business software developers new website

We need to redesign our website. Our current website is http://www.plovencast.example/index.html, which is outdated and needs a new look. We moved out from web design and have concentrated more on the back end of the systems, for example, system support and security and cloud-based applications. Our major clients include both private and government sectors. We would like to see some designs that are all in one page, simple and clean. Prefer illustrator or obstructed images instead of real-life photos. Must look futuristic yet friendly. Attached the new logo for your references and good luck.

Target Market(s)

Medium to big company for their IT or data management. Either improve or upgrade their current system.

Industry/Entity Type

Business Software

Number of Pages Required

1 page

Colors

Designer to choose colors to be used in the design.

Requirements
Must have
• Simple and clean. Individual assets must be provided in the correct size and format(png or jpeg). Prefer Goggle fonts. Even though the logo color is red, grey and black, still prefer some modern colors that go well with red. When design, must consider the possibility to convert it into responsive.
Nice to have
• White background
Should not have
• real life photos, no slider

```html
<!DOCTYPE html>
<html lang="en">
<head>
<meta charset="utf-8">
<title>PlovenCast – Business Software</title>
<link href="https://fonts.googleapis.com/css2?family=Roboto:wght@300;400;500;700&display=swap" rel="stylesheet">
<style>
:root{
  --red:#e52f3d;
  --ink:#2b2b2b;
  --text:#444;
  --muted:#777;
  --icon:#555;
  --line:#e4e4e4;
  --footer:#2d2a2b;
  --white:#fff;
  --green:#2bb673;
}
*{margin:0;padding:0;box-sizing:border-box}
html,body{width:1200px;height:3525px;overflow:hidden;background:var(--white)}
body{font-family:'Roboto',sans-serif;color:var(--text);position:relative}
.abs{position:absolute}
a{color:inherit;text-decoration:none}

/* header */
.brand{left:88px;top:16px;font-size:28px;font-weight:400;color:var(--ink);letter-spacing:-.3px;display:flex;align-items:center;gap:8px}
.brand-dot{width:12px;height:12px;border-radius:50%;background:var(--red)}
.nav{top:26px;left:585px;font-size:13px;font-weight:500;color:var(--ink)}
.nav a{position:absolute;white-space:nowrap}
.nav .active{color:var(--red)}

/* hero */
.hero-art{left:0;top:0}
.hero-title{left:88px;top:326px;color:var(--ink);font-weight:400;line-height:1}
.hero-title .small{display:block;font-size:44px}
.hero-title .big{display:block;font-size:68px;margin-top:0}
.hero-title .big b{color:var(--red);font-weight:400}
.hero-text{left:89px;top:440px;width:420px;font-size:14.5px;line-height:22px;color:var(--text)}
.btn{display:inline-flex;align-items:center;justify-content:center;background:var(--red);color:var(--white);font-weight:700;font-size:13px;border-radius:17px;height:32px}
.hero-btn{left:89px;top:493px;width:120px}

.section-title{width:100%;text-align:center;font-size:36px;font-weight:500;color:var(--ink);left:0}
.company-text{left:0;width:100%;top:865px;text-align:center;font-size:15px;line-height:22px;color:var(--text)}
.company-btn{left:541px;top:922px;width:120px}

/* services */
.service-mark{left:442px;top:1088px;width:312px;height:312px;border-radius:50%;background:var(--red);display:flex;align-items:center;justify-content:center;color:var(--white);font-size:38px;font-weight:500}
.service{font-size:16px;color:var(--text);white-space:nowrap}
.service.left{text-align:right;width:300px;left:4px}
.service.right{left:905px}

/* clients */
.clients{left:0;top:1512px;width:1200px;height:414px;background:linear-gradient(100deg,#e22f3e 0%,#d9313c 45%,#e63240 100%)}
.clients-title{left:88px;top:1660px;font-size:36px;font-weight:500;color:var(--white)}
.clients-text{left:88px;top:1712px;width:396px;font-size:15px;line-height:22px;color:var(--white);text-align:justify}
.client-tile{top:1668px;width:172px;height:137px;border:4px solid var(--white)}

/* news */
.card{top:2073px;width:324px;height:435px;background:var(--white);box-shadow:0 10px 30px rgba(0,0,0,.08)}
.card-img{width:324px;height:243px;display:block}
.card-meta{position:absolute;left:27px;top:268px;font-size:11px;color:var(--muted)}
.card-meta i{display:inline-block;width:3px;height:3px;border-radius:50%;background:#bbb;margin:0 6px 2px;vertical-align:middle}
.card-title{position:absolute;left:27px;top:298px;width:270px;font-size:19px;line-height:28px;font-weight:500;color:var(--ink)}
.tag{position:absolute;left:27px;top:374px;height:22px;padding:0 21px;border-radius:11px;font-size:9px;font-weight:500;display:flex;align-items:center;letter-spacing:.3px}
.tag.blog{background:#fdeaec;color:var(--red)}
.tag.news{background:#e4f7ed;color:var(--green)}
.news-more{left:0;width:100%;top:2535px;text-align:center;font-size:14px;color:var(--text)}
.news-more a{color:var(--red);text-decoration:underline}

/* faq & testimonials */
.block-title{font-size:36px;font-weight:500;color:var(--ink)}
.faq-item{left:88px;width:460px;font-size:14px;color:var(--text);display:flex;justify-content:space-between}
.faq-item .plus{color:var(--red);font-size:18px;font-weight:500;margin-right:14px;line-height:14px}
.faq-line{left:88px;top:2762px;width:460px;height:1px;background:var(--line)}
.quote{left:606px;top:2722px;width:505px;font-size:14px;line-height:21.5px;color:var(--text);text-align:justify}
.quote-name{left:606px;top:2812px;font-size:14.5px;color:var(--red);font-weight:500}
.quote-site{left:606px;top:2830px;font-size:14.5px;color:var(--ink)}

/* footer */
.footer{left:0;top:2990px;width:1200px;height:535px;background:var(--footer)}
.foot-title{font-size:36px;font-weight:500;color:var(--white);top:3128px}
.philosophy{left:88px;top:3184px;width:478px;font-size:14px;line-height:21.5px;color:#e6e6e6;text-align:justify}
.phone{left:88px;font-size:14px;color:#e6e6e6;display:flex;align-items:center;gap:6px}
.socials{left:88px;top:3345px;display:flex;gap:14px}
.socials i{width:9px;height:9px;border-radius:50%;background:var(--white)}
.field{font-size:13px;color:#bdbdbd;border-bottom:1px solid #5a5657}
.send{left:612px;top:3337px;width:139px;height:33px;border-radius:0;font-size:13px}
.foot-line{left:88px;top:3474px;width:1023px;height:1px;background:#4a4647}
.copyright{left:0;width:100%;top:3492px;text-align:center;font-size:13px;color:#e6e6e6}
.to-top{left:1125px;top:3458px;width:34px;height:34px;border-radius:50%;background:var(--red);display:flex;align-items:center;justify-content:center}
</style>
</head>
<body>

<header>
  <div class="abs brand"><span>plovencast</span><span class="brand-dot"></span><span>example</span></div>
  <nav class="abs nav">
    <a class="active" style="left:0">HOME</a>
    <a style="left:65px">ABOUT US</a>
    <a style="left:155px">OUR SERVICES</a>
    <a style="left:274px">OUR CLIENTS</a>
    <a style="left:383px">NEWS</a>
    <a style="left:448px">CONTACT US</a>
  </nav>
</header>

<svg class="abs hero-art" width="1200" height="970" role="img" aria-label="Abstract illustration of a laptop running cloud software">
  <defs>
    <linearGradient id="heroGrad" x1="0" y1="0" x2="1" y2="1">
      <stop offset="0" stop-color="#1d7d98"/>
      <stop offset=".35" stop-color="#155a72"/>
      <stop offset=".55" stop-color="#c8262f"/>
      <stop offset=".8" stop-color="#2a2a2e"/>
      <stop offset="1" stop-color="#1b1b1d"/>
    </linearGradient>
  </defs>
  <path d="M1200,267 L975,140 Q900,98 821,101 C650,108 527,230 527,397 C527,520 600,600 690,650 L1200,958 Z" fill="url(#heroGrad)"/>
</svg>

<h1 class="abs hero-title"><span class="small">Welcome to</span><span class="big">Plove<b>n</b>Cast</span></h1>
<p class="abs hero-text">We build secure back-end systems, system support and cloud-based applications for businesses of all sizes.</p>
<a class="abs btn hero-btn">READ MORE</a>

<h2 class="abs section-title" style="top:815px">Our Company</h2>
<p class="abs company-text">Plovencast.example is an Australian based Business Software Company that provides system<br>support, security and cloud-based applications for private and government clients.</p>
<a class="abs btn company-btn">READ MORE</a>

<h2 class="abs section-title" style="top:1027px">Our Services</h2>
<div class="abs service-mark">PlovenCast</div>

<div class="abs service left" style="top:1133px">System Support</div>
<svg class="abs" style="left:326px;top:1110px" width="78" height="72" fill="none" stroke="var(--icon)" stroke-width="4">
  <rect x="3" y="6" width="72" height="48"/><path d="M39 54v8M24 66h30"/><path d="M24 30l10 10 20-20"/>
</svg>
<div class="abs service left" style="top:1231px">Software Development</div>
<svg class="abs" style="left:323px;top:1215px" width="78" height="70" fill="none" stroke="var(--icon)" stroke-width="4">
  <rect x="3" y="3" width="72" height="52"/><path d="M39 55v8M24 66h30"/><path d="M26 20l-9 9 9 9M52 20l9 9-9 9M43 16l-8 26"/>
</svg>
<div class="abs service left" style="top:1337px">Cloud Applications</div>
<svg class="abs" style="left:324px;top:1318px" width="80" height="56" fill="none" stroke="var(--red)" stroke-width="4">
  <path d="M20 50a14 14 0 0 1 0-28 18 18 0 0 1 34-6 14 14 0 0 1 6 34z"/>
</svg>

<svg class="abs" style="left:809px;top:1110px" width="68" height="70" fill="none" stroke="var(--icon)" stroke-width="4">
  <ellipse cx="34" cy="12" rx="28" ry="9"/><path d="M6 12v46c0 5 12 9 28 9s28-4 28-9V12M6 35c0 5 12 9 28 9s28-4 28-9"/>
</svg>
<div class="abs service right" style="top:1131px">Data Management</div>
<svg class="abs" style="left:812px;top:1208px" width="64" height="72" fill="none" stroke="var(--icon)" stroke-width="4">
  <path d="M32 3l26 10v20c0 18-12 30-26 36C18 63 6 51 6 33V13z"/><rect x="22" y="32" width="20" height="16" fill="var(--icon)"/><path d="M26 32v-6a6 6 0 0 1 12 0v6"/>
</svg>
<div class="abs service right" style="top:1231px">System Security</div>
<svg class="abs" style="left:812px;top:1303px" width="68" height="68" fill="var(--icon)">
  <path d="M20 20a10 10 0 0 1 14-14 12 12 0 0 1 18 10 8 8 0 0 1 0 12H20a7 7 0 0 1 0-8z"/>
  <rect x="32" y="28" width="4" height="10"/><rect x="10" y="36" width="48" height="4"/>
  <rect x="2" y="42" width="16" height="24"/><rect x="26" y="42" width="16" height="24"/><rect x="50" y="42" width="16" height="24"/>
</svg>
<div class="abs service right" style="top:1337px">Hosting Solutions</div>

<section>
  <div class="abs clients" role="img" aria-label="Red toned abstract illustration of servers and data screens"></div>
  <h2 class="abs clients-title">Our Clients</h2>
  <p class="abs clients-text">Engineering, security expertise and experienced management help us to provide our private and government clients with reliable, high-grade back-end systems and cloud applications, which save them time and money, protect their data and bring robust functionality into their businesses.</p>
  <div class="abs client-tile" style="left:554px;background:linear-gradient(#f0f0f0,#f6a04a 40%,#f2f2f2)" role="img" aria-label="Screenshot of a client system"></div>
  <div class="abs client-tile" style="left:747px;background:linear-gradient(160deg,#eef2f7,#ffffff 55%,#d8e4ee)" role="img" aria-label="Screenshot of a client system"></div>
  <div class="abs client-tile" style="left:940px;background:linear-gradient(#4aa83a 25%,#ffffff 25%)" role="img" aria-label="Screenshot of a client system"></div>
</section>

<h2 class="abs section-title" style="top:2010px">Our News</h2>
<article class="abs card" style="left:88px">
  <div class="card-img" style="background:linear-gradient(#cfd3d2,#8a8f8c)" role="img" aria-label="Illustration for a blog post on system support"></div>
  <div class="card-meta">by Lena Marsh<i></i>17 hours ago</div>
  <h3 class="card-title">Blog 1 heading: Some news heading goes here...</h3>
  <span class="tag blog">BLOG</span>
</article>
<article class="abs card" style="left:438px">
  <div class="card-img" style="background:linear-gradient(#eeeae4,#b9b3aa)" role="img" aria-label="Illustration for a news post on cloud applications"></div>
  <div class="card-meta">by Tom Irving<i></i>18 hours ago</div>
  <h3 class="card-title">News 2 heading: Some news heading goes here...</h3>
  <span class="tag news">NEWS</span>
</article>
<article class="abs card" style="left:785px">
  <div class="card-img" style="background:linear-gradient(90deg,#5a86b5,#d9dde2 50%,#3c5d99)" role="img" aria-label="Illustration for a blog post on data security"></div>
  <div class="card-meta">by Ravi Okafor<i></i>17 hours ago</div>
  <h3 class="card-title">Blog 3 heading: Some news heading goes here...</h3>
  <span class="tag blog">BLOG</span>
</article>
<p class="abs news-more">Interested in our News and Blogs ? <a>Check out more</a></p>

<h2 class="abs block-title" style="left:88px;top:2668px">Faq</h2>
<div class="abs faq-item" style="top:2731px"><span>How much does a support plan with Plovencast.example cost?</span><span class="plus">+</span></div>
<div class="abs faq-line"></div>
<div class="abs faq-item" style="top:2774px"><span>How long does it take to move our system to the cloud?</span><span class="plus">+</span></div>

<h2 class="abs block-title" style="left:603px;top:2668px">Testimonials</h2>
<p class="abs quote">Now that our new system is live I would like to formally record my appreciation for the excellent service that Plovencast.example provided and for your flexibility during the work. You were responsive to our needs and the support your technical team provided was second to none. Thanks!</p>
<div class="abs quote-name">Owen Tally</div>
<div class="abs quote-site">www.brightpartsco.example</div>

<footer class="abs footer"></footer>
<h2 class="abs foot-title" style="left:88px">Philosophy</h2>
<p class="abs philosophy">As software developers, we understand that a secure and reliable back-end system is a vital component of every modern company today. This is why our development and support team work with all of our clients to ensure their systems stay fast, safe and ready to grow.</p>
<div class="abs phone" style="top:3281px"><svg width="12" height="12" viewBox="0 0 24 24"><path fill="var(--red)" d="M6.6 10.8a15 15 0 0 0 6.6 6.6l2.2-2.2c.3-.3.7-.4 1-.2 1.1.4 2.3.6 3.6.6.6 0 1 .4 1 1V20c0 .6-.4 1-1 1A17 17 0 0 1 3 4c0-.6.4-1 1-1h3.5c.6 0 1 .4 1 1 0 1.3.2 2.5.6 3.6.1.3 0 .7-.2 1z"/></svg>Office number: +61 7 5550 0142</div>
<div class="abs phone" style="top:3302px"><svg width="12" height="12" viewBox="0 0 24 24"><path fill="var(--red)" d="M6.6 10.8a15 15 0 0 0 6.6 6.6l2.2-2.2c.3-.3.7-.4 1-.2 1.1.4 2.3.6 3.6.6.6 0 1 .4 1 1V20c0 .6-.4 1-1 1A17 17 0 0 1 3 4c0-.6.4-1 1-1h3.5c.6 0 1 .4 1 1 0 1.3.2 2.5.6 3.6.1.3 0 .7-.2 1z"/></svg>Mobile number: +61 0400 555 318</div>
<div class="abs socials" aria-label="Social links"><i></i><i></i><i></i><i></i></div>

<h2 class="abs foot-title" style="left:610px">Quick Contact</h2>
<div class="abs field" style="left:612px;top:3193px;width:236px;height:27px;padding-left:13px">Name</div>
<div class="abs field" style="left:877px;top:3193px;width:232px;height:27px;padding-left:13px">Email</div>
<div class="abs field" style="left:612px;top:3233px;width:497px;height:91px;padding-left:13px">Message</div>
<a class="abs btn send">SEND MESSAGE</a>

<div class="abs foot-line"></div>
<p class="abs copyright">Copyright 2019 | Plovencast.example</p>
<a class="abs to-top" aria-label="Back to top"><svg width="12" height="8" viewBox="0 0 12 8"><path d="M1 7l5-5 5 5" fill="none" stroke="#fff" stroke-width="2"/></svg></a>

</body>
</html>
```